Logo, Web and Mobile Designs for enterprise social media platform

All the details are in the attached document, please start reading the scope document first which explains what is this project about and the details about the needed deliverables, after that please read the UI_Requirements document which will detail what is expected regarding the coded web version since this is a coded contest, it is very important that you meet the UI requirements or suggest something else but we will need to agree first before working on the coded version

Good Luck

Target Market(s)

Enterprise Social Media

Industry/Entity Type

Media

Coding

Coded - Design and coding required

Number of Pages Required

5+ page

Font styles to use
Sans Serif

Requirements
Must have
• All the must haves are listed in the scope document so please check before you start

```html
<!DOCTYPE html>
<html lang="en">
<head>
<meta charset="utf-8">
<title>Teamora – Sign In</title>
<link href="https://fonts.googleapis.com/css2?family=Roboto:wght@400;500&family=Open+Sans:wght@400&display=swap" rel="stylesheet">
<style>
  :root {
    --page-bg: #f6f6f6;
    --header-bg: #fafafa;
    --rule: #e3e3e3;
    --heading: #5a5a5a;
    --label: #555555;
    --icon: #9a9a9a;
    --field-bg: #ffffff;
    --field-border: #e6e6e6;
    --accent-orange: #e88c00;
    --accent-blue: #219dcf;
    --footer-bg: #1f8ab8;
    --footer-text: #ffffff;
    --brand: #2a9fd6;
  }
  * { box-sizing: border-box; margin: 0; padding: 0; }
  html, body { width: 768px; height: 1200px; overflow: hidden; }
  body {
    position: relative;
    font-family: "Roboto", Arial, sans-serif;
    background: linear-gradient(160deg, #f9f9f9 0%, #f1f1f1 50%, #f7f7f7 100%);
    color: var(--label);
  }
  .site-header {
    position: absolute; left: 0; top: 0; width: 768px; height: 151px;
    background: var(--header-bg);
    border-bottom: 2px solid var(--rule);
  }
  .header-cell { position: absolute; top: 0; height: 149px; display: flex; align-items: center; justify-content: center; }
  .header-home { left: 0; width: 138px; border-right: 2px solid var(--rule); }
  .header-brand { left: 138px; width: 496px; gap: 16px; }
  .header-menu { left: 634px; width: 134px; border-left: 2px solid var(--rule); }
  .brand-dot { width: 54px; height: 54px; border-radius: 50%; background: var(--accent-orange); }
  .brand-name { font-size: 50px; font-weight: 500; color: var(--brand); letter-spacing: 0.5px; }

  .section-title {
    position: absolute; left: 32px; font-size: 35px; font-weight: 400;
    color: var(--heading); letter-spacing: 1px;
  }
  .rule { position: absolute; left: 0; width: 768px; height: 2px; background: var(--rule); }

  .field-label { position: absolute; font-size: 22px; color: var(--label); }
  .field-label .req { font-size: 16px; vertical-align: 3px; margin-left: 3px; }
  .field {
    position: absolute; background: var(--field-bg);
    border: 2px solid var(--field-border); border-radius: 6px;
  }
  .field svg { position: absolute; right: 22px; top: 50%; transform: translateY(-50%); }

  .remember { position: absolute; left: 114px; top: 526px; display: flex; align-items: center; gap: 8px;
    font-family: "Open Sans", Arial, sans-serif; font-size: 21px; color: var(--label); }
  .remember .radio { width: 24px; height: 24px; border: 2px solid #555; border-radius: 50%; }
  .forgot { position: absolute; left: 338px; top: 526px; font-family: "Open Sans", Arial, sans-serif;
    font-size: 21px; color: var(--label); text-decoration: underline; }

  .btn { position: absolute; border-radius: 5px; color: #fff; font-size: 22px;
    display: flex; align-items: center; justify-content: center; letter-spacing: 0.5px; }
  .btn-signin { left: 537px; top: 511px; width: 179px; height: 61px; background: var(--accent-orange); }
  .btn-register { left: 526px; top: 861px; width: 196px; height: 64px; background: var(--accent-blue); }

  .site-footer { position: absolute; left: 0; top: 963px; width: 768px; height: 237px;
    background: var(--footer-bg); color: var(--footer-text); }
  .social { position: absolute; top: 50px; left: 0; width: 768px; display: flex; justify-content: center; gap: 20px; }
  .social span { width: 38px; height: 38px; border-radius: 7px; background: var(--footer-text); }
  .footer-nav { position: absolute; top: 112px; width: 768px; text-align: center; font-size: 22px; font-weight: 500; }
  .footer-nav .sep { margin: 0 16px; }
  .copyright { position: absolute; top: 162px; width: 768px; text-align: center; font-size: 21px; font-weight: 500; }
</style>
</head>
<body>
  <header class="site-header">
    <div class="header-cell header-home">
      <svg width="34" height="30" viewBox="0 0 34 30"><path d="M17 2 L2 15 h5 v13 h8 v-9 h4 v9 h8 V15 h5 z" fill="#6b6b6b"/></svg>
    </div>
    <div class="header-cell header-brand">
      <span class="brand-dot"></span>
      <span class="brand-name">Teamora</span>
    </div>
    <div class="header-cell header-menu">
      <svg width="32" height="28" viewBox="0 0 32 28" fill="#7a7a7a"><rect y="1" width="32" height="5" rx="1"/><rect y="11.5" width="32" height="5" rx="1"/><rect y="22" width="32" height="5" rx="1"/></svg>
    </div>
  </header>

  <main>
    <section class="signin">
      <h1 class="section-title" style="top:189px">TEAMORA SIGN IN</h1>
      <div class="rule" style="top:260px"></div>

      <label class="field-label" style="left:34px;top:334px">User Name<span class="req">*</span></label>
      <div class="field" style="left:194px;top:312px;width:525px;height:72px">
        <svg width="20" height="24" viewBox="0 0 20 24" fill="var(--icon)"><circle cx="10" cy="7" r="6"/><path d="M0 24 q0-10 10-10 q10 0 10 10z"/></svg>
      </div>

      <label class="field-label" style="left:50px;top:433px">Password<span class="req">*</span></label>
      <div class="field" style="left:194px;top:411px;width:525px;height:72px">
        <svg width="26" height="26" viewBox="0 0 26 26" fill="var(--icon)">
          <circle cx="13" cy="3" r="2.5"/><circle cx="20" cy="6" r="2.3"/><circle cx="23" cy="13" r="2.1"/><circle cx="20" cy="20" r="1.9"/>
          <circle cx="13" cy="23" r="1.7"/><circle cx="6" cy="20" r="1.5"/><circle cx="3" cy="13" r="1.3"/><circle cx="6" cy="6" r="1.1"/>
        </svg>
      </div>

      <div class="remember"><span class="radio"></span>Remember me</div>
      <span class="forgot">Forgot Password</span>
      <span class="btn btn-signin">SIGN IN</span>
    </section>

    <div class="rule" style="top:618px"></div>

    <section class="signup">
      <h2 class="section-title" style="top:651px">TEAMORA SIGN UP</h2>
      <div class="rule" style="top:728px"></div>

      <label class="field-label" style="left:38px;top:789px">E - Mail<span class="req">*</span></label>
      <div class="field" style="left:199px;top:767px;width:525px;height:72px">
        <svg width="26" height="20" viewBox="0 0 26 20" fill="none" stroke="var(--icon)" stroke-width="2"><rect x="1" y="1" width="24" height="18" rx="2"/><path d="M1 3 L13 12 L25 3"/></svg>
      </div>
      <span class="btn btn-register">REGISTER</span>
    </section>
  </main>

  <footer class="site-footer">
    <div class="social" aria-label="Social links">
      <span></span><span></span><span></span><span></span><span></span>
    </div>
    <nav class="footer-nav">
      Home<span class="sep">/</span>Contact<span class="sep">/</span>Topics<span class="sep">/</span>Posts &amp; Comments<span class="sep">/</span>Videos Links
    </nav>
    <p class="copyright">Copyright @ 2015 - 2015.Teamora. All Rights Reserved.</p>
  </footer>
</body>
</html>
```